Website for "Nodo de Soluciones Verdantes"

We need a new web design for an enterprise dedicated to environment and energy saving engineering, based in Monterrey, Mexico.
They offer consulting services, mainly to enhance building designs, and they are also resellers for several products in the energy saving field.

The final design should be oriented to engineers and architects, and should communicate professionalism, innovation, environment care.

Here is the website of a partner enterprise, which does pretty much the same:

http://www.cirelumen.com/

Target Market(s)

mainly architects and engineers looking for solutions on energy efficiency building

Industry/Entity Type

Environment

Requirements
Must have
• Entry page must be quite graphical and intuitive, must have a "products listing" and a "projects portfolio".

```html
<!DOCTYPE html>
<html lang="en">
<head>
<meta charset="utf-8">
<title>Nodo de Soluciones Verdantes — Contact</title>
<link rel="stylesheet" href="https://fonts.googleapis.com/css2?family=PT+Sans:wght@400;700&family=Source+Sans+3:wght@400;600&display=swap">
<style>
:root{
  --orange:#f26f21;
  --orange-light:#f58a3c;
  --orange-dark:#e0601a;
  --purple:#4a4592;
  --purple-dark:#3a3580;
  --green:#7cc242;
  --teal:#1aa3b0;
  --text:#555;
  --muted:#777;
  --line:#cfcfcf;
  --band:#f4f4f4;
}
*{margin:0;padding:0;box-sizing:border-box}
html,body{width:961px;height:1200px;overflow:hidden;background:#fff}
body{position:relative;font-family:"Source Sans 3",Arial,sans-serif;color:var(--text)}
.abs{position:absolute}
.top-rule{left:0;top:0;width:961px;height:5px;background:var(--orange)}

/* header */
.brand{left:98px;top:36px;display:flex;align-items:center;gap:10px}
.brand-dot{width:42px;height:42px;border-radius:50%;background:var(--purple)}
.brand-name{font-family:"PT Sans",sans-serif;font-weight:700;font-size:17px;line-height:19px;color:var(--purple);width:170px}
.social{top:17px;display:flex;gap:8px;left:776px}
.social span{width:20px;height:20px;border-radius:3px}
.search{left:543px;top:59px;width:176px;height:29px;border:1px solid #ddd;border-radius:4px;box-shadow:0 3px 4px rgba(0,0,0,.08);font-size:9px;color:#666;padding:10px 0 0 13px}
.search svg{position:absolute;right:10px;top:7px}
.hotline{right:106px;top:52px;text-align:right}
.hotline .label{font-size:13px;color:var(--green)}
.hotline .num{font-size:20px;color:var(--teal);line-height:20px}

/* hero */
.hero{left:0;top:141px;width:961px;height:345px;background:linear-gradient(180deg,#5fb5ee 0%,#bfe3f8 45%,#eaf6fd 68%,#7dc63a 76%,#4f9b1d 100%)}
.hero-title{left:115px;top:262px;font-family:"PT Sans",sans-serif;font-size:26px;color:#222}
.hero-text{left:116px;top:294px;font-size:11.5px;line-height:18.5px;color:#222;width:300px}
.hero-nav{top:346px;width:25px;height:25px;border-radius:50%;background:#5c5c5c;display:flex;align-items:center;justify-content:center}
.hero-shadow{left:70px;top:484px;width:830px;height:14px;background:radial-gradient(ellipse at top,rgba(0,0,0,.18),transparent 70%)}

/* nav */
.main-nav{left:95px;top:121px;width:770px;height:39px;background:var(--purple);display:flex;font-family:"PT Sans",sans-serif;font-weight:700;font-size:14px;color:#fff;box-shadow:0 4px 8px rgba(0,0,0,.25)}
.main-nav a{color:#fff;text-decoration:none;display:flex;align-items:center;justify-content:center;padding:0 21px}
.main-nav a.active{background:linear-gradient(#8bc94b,#6cb33a);width:110px;padding:0}

/* contact section */
.section-title{left:122px;top:516px;font-size:23px;color:var(--orange)}
.form-lead{left:124px;top:572px;font-size:15.5px;color:#777}
.label{left:124px;font-size:11px;color:#555}
.field{left:124px;width:196px;height:16px;border:1px solid #bbb}
.btn{background:var(--purple);color:#fff;border:1px solid var(--purple-dark);border-radius:5px;font-size:12px;display:flex;align-items:center;justify-content:center;gap:6px}
.divider-v{width:1px;background:var(--line)}
.map{left:469px;top:595px;width:202px;height:202px;background:#e7e4dd;border:1px solid #ccc}
.details-title{left:698px;top:690px;display:flex;align-items:center;gap:9px;font-size:15.5px;color:#666}
.details-title .icon{width:20px;height:20px;border-radius:4px;background:#e2e2e2;display:flex;align-items:center;justify-content:center}
.details{left:702px;top:724px;font-size:10px;line-height:19.2px;color:#444}

/* partners */
.partners{left:0;top:871px;width:961px;height:94px;background:var(--band)}
.partners h2{position:absolute;top:4px;width:100%;text-align:center;font-weight:400;font-size:18px;color:var(--orange)}
.partner-row{position:absolute;left:135px;top:35px;display:flex;gap:24px;align-items:center}
.partner-row span{width:88px;height:28px;border-radius:4px;background:#c9c9c9}
.arrow{top:28px;font-size:24px;color:var(--orange);font-family:"PT Sans",sans-serif;font-weight:700}

/* footer */
.footer{left:0;top:965px;width:961px;height:191px;background:linear-gradient(180deg,var(--orange),var(--orange-light) 60%,var(--orange))}
.footer h3{position:absolute;top:13px;font-weight:400;font-size:17.5px;color:#fff}
.quick{position:absolute;top:40px;font-size:12px;line-height:19.2px;color:#fff}
.divider-f{position:absolute;top:15px;width:1px;height:170px;background:rgba(0,0,0,.1)}
.follow{position:absolute;left:368px;display:flex;align-items:center;gap:16px;font-size:12px;color:#fff}
.follow i{width:32px;height:32px;border-radius:2px;display:block}
.f-input{position:absolute;left:616px;width:200px;background:#fff;border-radius:4px;font-size:9px;color:#999;padding:7px 6px}
.footer .btn{position:absolute;left:749px;top:159px;width:67px;height:25px;font-size:13px}
.bottom{left:0;top:1156px;width:961px;height:44px;background:var(--orange-dark);font-size:10px;color:#fff;padding:15px 0 0 99px;word-spacing:2px}
</style>
</head>
<body>
<div class="abs top-rule"></div>

<header>
  <div class="abs brand"><span class="brand-dot"></span><span class="brand-name">Nodo de Soluciones Verdantes</span></div>
  <div class="abs social"><span style="background:#5aa9c9"></span><span style="background:#3b5a98"></span><span style="background:#f08a24"></span></div>
  <div class="abs search">Search
    <svg width="14" height="14" viewBox="0 0 14 14"><circle cx="6" cy="6" r="4.5" fill="none" stroke="#777" stroke-width="1.5"/><line x1="9.3" y1="9.3" x2="13" y2="13" stroke="#777" stroke-width="2"/></svg>
  </div>
  <div class="abs hotline"><div class="label">Contact Us</div><div class="num">1800 614 7720</div></div>
</header>

<div class="abs hero" role="img" aria-label="Bright blue sky over a green meadow with a lone tree and a small house"></div>
<h1 class="abs hero-title" style="font-weight:400">Duis tincidunt lectus quis</h1>
<p class="abs hero-text">Vivamus porttitor purus nisi eleifend libero, a tempus libero lectus feugiat felis Morbi diam mauris viverra.</p>
<div class="abs hero-nav" style="left:120px"><svg width="8" height="8"><path d="M6 0L1 4L6 8Z" fill="#fff"/></svg></div>
<div class="abs hero-nav" style="left:149px"><svg width="8" height="8"><path d="M2 0L7 4L2 8Z" fill="#fff"/></svg></div>
<div class="abs hero-shadow"></div>

<nav class="abs main-nav">
  <a class="active" href="#">Home</a><a href="#">The Company</a><a href="#">Products</a><a href="#">Project&nbsp;Portfolio</a><a href="#">Photo Gallery</a><a href="#">News</a><a href="#">Contacts</a>
</nav>

<main>
  <h2 class="abs section-title" style="font-weight:400">CONTACT US</h2>
  <p class="abs form-lead">Kindly post your valuable Suggestions &amp; Query</p>
  <span class="abs label" style="top:607px">Enter your Name</span>
  <div class="abs field" style="top:623px"></div>
  <span class="abs label" style="top:645px">Enter your Email</span>
  <div class="abs field" style="top:663px"></div>
  <span class="abs label" style="top:683px">Enter your Phone Number</span>
  <div class="abs field" style="top:703px"></div>
  <span class="abs label" style="top:722px">Add Your Comments Here:</span>
  <div class="abs field" style="top:737px;height:38px"></div>
  <div class="abs btn" style="left:166px;top:794px;width:105px;height:22px">Submit Query <svg width="5" height="8"><path d="M0 0L5 4L0 8Z" fill="#fff"/></svg></div>

  <div class="abs divider-v" style="left:452px;top:583px;height:250px"></div>
  <div class="abs map" role="img" aria-label="Street map showing the office location"></div>

  <div class="abs details-title"><span class="icon"><svg width="12" height="12" viewBox="0 0 12 12"><path d="M2 1h3l1 3-2 1a7 7 0 0 0 3 3l1-2 3 1v3c-6 1-10-3-9-9z" fill="#fff"/></svg></span>Contact Details</div>
  <div class="abs details">#18 Calle Encino, Monterrey,<br>Phone: +52 818 340 2215<br>Tollfree: (800) 41027735<br>E-mail: info@nodoverdante.com</div>
</main>

<section class="abs partners">
  <h2>Our Partners</h2>
  <span class="abs arrow" style="left:92px">‹</span>
  <div class="partner-row"><span></span><span></span><span></span><span></span><span></span><span></span></div>
  <span class="abs arrow" style="left:842px">›</span>
</section>

<footer class="abs footer">
  <h3 style="left:90px">QUICK LINKS</h3>
  <div class="quick" style="left:96px">Home<br>the company<br>Products<br>project portfolio</div>
  <div class="quick" style="left:225px">Phot gallary<br>News<br>Contact</div>
  <div class="divider-f" style="left:340px"></div>
  <h3 style="left:364px">FOLLOW US</h3>
  <div class="follow" style="top:48px"><i style="background:#3b5a98"></i>Share on Circlebook</div>
  <div class="follow" style="top:87px"><i style="background:#3aa4dd"></i>Follow us on Chirper</div>
  <div class="follow" style="top:126px"><i style="background:#f0812a"></i>Rss feed</div>
  <div class="divider-f" style="left:588px"></div>
  <h3 style="left:615px">CONTACT US</h3>
  <div class="f-input" style="top:44px;height:27px">Name</div>
  <div class="f-input" style="top:77px;height:27px">Email</div>
  <div class="f-input" style="top:110px;height:43px">Message</div>
  <div class="btn">Submit</div>
</footer>
<div class="abs bottom">Copyright © 2013 &nbsp;&nbsp;www.nodoverdante.com &nbsp;&nbsp;&nbsp;All rights reserved.</div>
</body>
</html>
```